Website Design for Forklift Training Company

DO NOT CONTACT PRIVATELY. ONLY SUBMISSIONS HERE WILL BE CONSIDERED

I need a design for a website that offers forklift training courses.

The company offers accredited, onsite forklift training that are customized for the needs of each individual company. The company offers a variety of courses to operate forklifts and other machinary.

About: "KVW Training Ltd delivers bespoke onsite forklift truck operator training throught the uk.
All our instructors have a wealth of knowledge and expertise to provide your company with all your forklift truck training requirements.
KVW Training Ltd is registered and accredited by plomvex standards so you can be rest assured that all forklift training is carried out the very highest standard"

I need the following pages designed:
> a) Home Page: Include a header image, ways to contact, about snippet, overview of courses, accreditation that will be received after completing the courses. (See attachments for samples)
> b) About Page
> c) Contact Us Page
> d) Course Page Template: A page that will be used as template for the courses offered. It should contain;
1. Cover image for the course
2. A description of the course
3. A table indicating the various course options
4. Course Objectives
5. What the trainee will receive after doing the course (example: a certification)

Industrial Businesses

4 page

Colors
0054AA
0677BA
7BADD7
CADEEF
E8F1F8
0094D4
00A9DD
6FCCEA
C7EBF8
E9F6FB

• - No Search bar

```html
<!DOCTYPE html>
<html lang="en">
<head>
<meta charset="utf-8">
<title>KVW Training Ltd – Forklift Truck Operator Training</title>
<link href="https://fonts.googleapis.com/css2?family=Oswald:wght@300;400&family=Montserrat:wght@400;600;700;800&family=Roboto:wght@400;500&display=swap" rel="stylesheet">
<style>
:root{
  --navy:#0054AA;
  --blue:#0677BA;
  --sky:#0094D4;
  --cyan:#00A9DD;
  --light-cyan:#6FCCEA;
  --pale:#E8F1F8;
  --pale-2:#EEF4FB;
  --ink:#153a6b;
  --text:#555c66;
  --slate:#2c3a4d;
  --orange:#F7941D;
  --footer:#0C3C8C;
  --white:#fff;
}
*{box-sizing:border-box;margin:0;padding:0}
html,body{width:1200px;height:3564px;overflow:hidden;background:var(--white)}
body{position:relative;font-family:"Montserrat",sans-serif;color:var(--text)}
.abs{position:absolute}
a{color:inherit;text-decoration:none}

/* header */
.site-header{position:absolute;left:0;top:0;width:1200px;height:83px;background:var(--white)}
.brand{left:111px;top:18px;font-family:"Oswald",sans-serif;font-weight:400;font-size:34px;color:var(--sky);letter-spacing:.5px}
.main-nav a{position:absolute;top:31px;font-family:"Oswald",sans-serif;font-weight:400;font-size:16px;color:var(--navy)}
.main-nav .active::after{content:"";position:absolute;left:-6px;right:-6px;top:48px;height:4px;background:var(--sky)}
.phone-pill{left:943px;top:24px;width:167px;height:38px;border-radius:19px;background:var(--sky);color:var(--white);font-family:"Oswald",sans-serif;font-size:16px;display:flex;align-items:center;justify-content:center;gap:8px}

/* hero */
.hero{left:0;top:83px;width:1200px;height:637px;background:linear-gradient(90deg,#0a5cb8 0%,#0a6ec4 40%,#3a78a8 60%,#7a7f78 80%,#5c6260 100%)}
.hero-photo{left:640px;top:0;width:560px;height:637px;background:linear-gradient(180deg,rgba(230,190,60,.35) 0%,rgba(40,70,120,.15) 40%,rgba(30,45,70,.35) 100%)}
.hero-eyebrow{left:108px;top:209px;font-family:"Oswald",sans-serif;font-weight:300;font-size:27px;letter-spacing:5px;color:var(--white);display:flex;align-items:center;gap:6px}
.hero-eyebrow::after{content:"";width:120px;height:1.5px;background:var(--white)}
.hero-title{left:106px;top:248px;font-family:"Montserrat",sans-serif;font-weight:800;font-size:45px;line-height:46px;color:var(--white)}
.btn-orange{left:105px;top:363px;width:172px;height:42px;border-radius:21px;background:var(--orange);color:var(--white);font-weight:700;font-size:13px;display:flex;align-items:center;justify-content:center;gap:8px}
.hero-arrow{top:268px}

/* about */
.about-figure{left:110px;top:866px;width:480px;height:400px}
.orbit-label{font-family:"Oswald",sans-serif;font-weight:400;font-size:16px;color:var(--navy);line-height:19px}
.eyebrow{font-family:"Oswald",sans-serif;font-weight:400;font-size:17px;letter-spacing:3px;color:var(--ink)}
.section-title{font-family:"Montserrat",sans-serif;font-weight:800;font-size:35px;color:var(--ink)}
.section-title .hl{color:var(--sky)}
.about-text{left:617px;width:460px;font-size:14px;line-height:23px;color:var(--text)}
.btn-outline{border:2px solid var(--sky);color:var(--sky);border-radius:24px;font-weight:700;font-size:13px;display:flex;align-items:center;justify-content:center}

/* courses */
.courses-band{left:0;top:1347px;width:1200px;height:110px;background:var(--pale-2)}
.courses-tab{left:457px;top:1305px;width:297px;height:44px;background:var(--pale-2);clip-path:polygon(14% 0,86% 0,100% 100%,0 100%)}
.course-col{top:1457px;width:400px;height:629px;color:var(--white)}
.col-forklift{left:0;background:linear-gradient(180deg,#0d5cc4 0%,#0a56b8 100%)}
.col-mewp{left:400px;background:linear-gradient(180deg,#05aaf0 0%,#0aa0e6 100%);border-left:2px solid #cfe6f7;border-right:2px solid #cfe6f7}
.col-other{left:802px;width:398px;background:linear-gradient(180deg,#34465b 0%,#2a384a 100%)}
.course-col h3{position:absolute;top:100px;font-family:"Oswald",sans-serif;font-weight:300;font-size:27px;letter-spacing:.2px}
.course-col h3::after{content:"";position:absolute;left:2px;top:48px;width:46px;height:3px;background:var(--white)}
.course-list{position:absolute;top:158px;list-style:none;font-family:"Roboto",sans-serif;font-size:12.5px}
.course-list li{height:23.1px;display:flex;align-items:center;gap:9px}
.tick{width:17px;height:17px;flex:none}
.btn-ghost{position:absolute;top:551px;width:151px;height:41px;border:2px solid var(--white);border-radius:21px;font-weight:700;font-size:13px;display:flex;align-items:center;justify-content:center}
.col-icon{position:absolute;top:33px}

/* accreditation */
.accred{left:0;top:2086px;width:1200px;height:712px;background:var(--pale-2)}
.accred-card{top:2324px;width:483px;height:379px;background:var(--white);padding:0 20px}
.accred-card p{position:absolute;left:35px;width:420px;font-size:11px;line-height:21.5px;color:var(--text)}
.partner-name{font-family:"Montserrat",sans-serif;font-weight:700;font-size:30px;color:var(--navy)}

/* contact */
.contact-photo{left:0;top:2798px;width:567px;height:589px}
.field{left:649px;width:426px;height:41px;background:#eef2f6;font-size:10.5px;color:#3b4350;padding:14px 0 0 20px}
.btn-submit{left:652px;top:3259px;width:153px;height:39px;border-radius:20px;background:var(--sky);color:var(--white);font-weight:700;font-size:11px;display:flex;align-items:center;justify-content:center}

/* footer */
.site-footer{left:0;top:3387px;width:1200px;height:177px;background:var(--footer);color:var(--white)}
.footer-nav a{position:absolute;top:44px;font-family:"Oswald",sans-serif;font-size:16px}
.copyright{position:absolute;left:0;width:1200px;top:82px;text-align:center;font-size:11px;color:#a8c3e8}
.social-dot{position:absolute;top:112px;width:23px;height:23px;border-radius:50%;background:var(--white)}
</style>
</head>
<body>

<header class="site-header">
  <div class="abs brand">KVW TRAINING LTD</div>
  <nav class="main-nav">
    <a class="active" href="#" style="left:425px">HOME</a>
    <a href="#" style="left:538px">ABOUT US</a>
    <a href="#" style="left:676px">COURSES</a>
    <a href="#" style="left:810px">CONTACT US</a>
  </nav>
  <a class="abs phone-pill" href="#">
    <svg width="18" height="18" viewBox="0 0 24 24"><path fill="#fff" d="M6.6 10.8a15.1 15.1 0 0 0 6.6 6.6l2.2-2.2a1 1 0 0 1 1-.25 11.4 11.4 0 0 0 3.6.57 1 1 0 0 1 1 1V20a1 1 0 0 1-1 1A17 17 0 0 1 3 4a1 1 0 0 1 1-1h3.5a1 1 0 0 1 1 1c0 1.25.2 2.45.57 3.57a1 1 0 0 1-.25 1z"/></svg>
    (122) 555 0142
  </a>
</header>

<section class="abs hero">
  <div class="abs hero-photo" role="img" aria-label="Smiling operator in hard hat and hi-vis vest driving a forklift in a warehouse"></div>
  <div class="abs hero-eyebrow">KVW TRAINING LTD</div>
  <h1 class="abs hero-title">FORKLIFT TRUCK<br>OPERATOR TRAINING</h1>
  <a class="abs btn-orange" href="#">CONTACT US
    <svg width="26" height="26" viewBox="0 0 26 26"><circle cx="13" cy="13" r="11" fill="none" stroke="#fff" stroke-width="1.6"/><path d="M7 13h11M14 9l4 4-4 4" fill="none" stroke="#fff" stroke-width="1.6"/></svg>
  </a>
  <svg class="abs hero-arrow" style="left:26px" width="22" height="36" viewBox="0 0 22 36"><path d="M17 4 5 18l12 14" fill="none" stroke="#fff" stroke-width="4"/></svg>
  <svg class="abs hero-arrow" style="left:1155px" width="22" height="36" viewBox="0 0 22 36"><path d="m5 4 12 14L5 32" fill="none" stroke="#fff" stroke-width="4"/></svg>
</section>

<section>
  <svg class="abs about-figure" viewBox="0 0 480 400" aria-hidden="true">
    <defs><linearGradient id="circleTone" x1="0" y1="0" x2="0" y2="1"><stop offset="0" stop-color="#1f7ad0"/><stop offset="1" stop-color="#0a58b4"/></linearGradient></defs>
    <path d="M75 335 A187 187 0 1 1 362 285" fill="none" stroke="var(--navy)" stroke-width="2"/>
    <circle cx="192" cy="193" r="173" fill="url(#circleTone)"/>
    <circle cx="111" cy="12" r="6" fill="#fff" stroke="var(--sky)" stroke-width="3"/>
    <circle cx="288" cy="20" r="6" fill="#fff" stroke="var(--sky)" stroke-width="3"/>
    <circle cx="365" cy="115" r="6" fill="#fff" stroke="var(--sky)" stroke-width="3"/>
  </svg>
  <div class="abs" role="img" aria-label="Yellow counterbalance forklift truck" style="left:180px;top:960px;width:390px;height:300px;border-radius:30px;background:radial-gradient(ellipse at 40% 55%,rgba(232,184,35,.95) 0%,rgba(201,155,28,.85) 35%,rgba(70,70,70,.5) 60%,rgba(0,0,0,0) 72%)"></div>
  <div class="abs orbit-label" style="left:188px;top:850px">FORKLIFT</div>
  <div class="abs orbit-label" style="left:374px;top:834px;text-align:center">MEWP<br>TRAINING</div>
  <div class="abs orbit-label" style="left:494px;top:965px">OTHER<br>TRAINING</div>

  <div class="abs eyebrow" style="left:612px;top:850px">WHO WE ARE</div>
  <h2 class="abs section-title" style="left:612px;top:870px"><span class="hl">ABOUT</span> KVW TRAINING</h2>
  <p class="abs about-text" style="top:948px">KVW Training Ltd delivers bespoke onsite forklift truck operator training throught the uk. All our instructors have a wealth of knowledge and expertise to provide your company with all your forklift truck training requirements.</p>
  <p class="abs about-text" style="top:1064px">KVW Training Ltd is registered and accredited by plomvex standards so you can be rest assured that all forklift training is carried out the very highest standard</p>
  <a class="abs btn-outline" href="#" style="left:612px;top:1160px;width:166px;height:47px">LEARN MORE</a>
</section>

<section>
  <div class="abs courses-tab"></div>
  <div class="abs courses-band"></div>
  <div class="abs eyebrow" style="left:0;width:1200px;text-align:center;top:1344px;font-size:16px">WHAT WE OFFER</div>
  <h2 class="abs section-title" style="left:0;width:1200px;text-align:center;top:1366px">OUR <span class="hl">COURSES</span></h2>
  <div class="abs" style="left:560px;top:1410px;width:80px;height:4px;background:var(--sky)"></div>

  <div class="abs course-col col-forklift">
    <svg class="col-icon" style="left:82px" width="86" height="52" viewBox="0 0 86 52" fill="none" stroke="#fff" stroke-width="2.4"><path d="M4 38V24l10-6h16V6h10l6 30H4M46 4v44h36M30 18l8 18"/><circle cx="14" cy="42" r="6"/><circle cx="38" cy="42" r="6"/></svg>
    <h3 style="left:80px">FORKLIFT TRAINING COURSES</h3>
    <ul class="course-list" style="left:84px">
      <li><svg class="tick" viewBox="0 0 18 18"><circle cx="9" cy="9" r="9" fill="#fff"/><path d="m5 9 3 3 5-6" stroke="#0a56b8" stroke-width="2" fill="none"/></svg>Torvin Truck Training Course</li>
      <li><svg class="tick" viewBox="0 0 18 18"><circle cx="9" cy="9" r="9" fill="#fff"/><path d="m5 9 3 3 5-6" stroke="#0a56b8" stroke-width="2" fill="none"/></svg>Corvex Lift Training course</li>
      <li><svg class="tick" viewBox="0 0 18 18"><circle cx="9" cy="9" r="9" fill="#fff"/><path d="m5 9 3 3 5-6" stroke="#0a56b8" stroke-width="2" fill="none"/></svg>Counterbalance Training Course</li>
      <li><svg class="tick" viewBox="0 0 18 18"><circle cx="9" cy="9" r="9" fill="#fff"/><path d="m5 9 3 3 5-6" stroke="#0a56b8" stroke-width="2" fill="none"/></svg>Ravel Truck Training Course</li>
      <li><svg class="tick" viewBox="0 0 18 18"><circle cx="9" cy="9" r="9" fill="#fff"/><path d="m5 9 3 3 5-6" stroke="#0a56b8" stroke-width="2" fill="none"/></svg>Kestra Crane Training Course</li>
      <li><svg class="tick" viewBox="0 0 18 18"><circle cx="9" cy="9" r="9" fill="#fff"/><path d="m5 9 3 3 5-6" stroke="#0a56b8" stroke-width="2" fill="none"/></svg>Llop Training Course</li>
      <li><svg class="tick" viewBox="0 0 18 18"><circle cx="9" cy="9" r="9" fill="#fff"/><path d="m5 9 3 3 5-6" stroke="#0a56b8" stroke-width="2" fill="none"/></svg>Halvek Truck Training Course</li>
      <li><svg class="tick" viewBox="0 0 18 18"><circle cx="9" cy="9" r="9" fill="#fff"/><path d="m5 9 3 3 5-6" stroke="#0a56b8" stroke-width="2" fill="none"/></svg>Order Picker Truck Training Course</li>
      <li><svg class="tick" viewBox="0 0 18 18"><circle cx="9" cy="9" r="9" fill="#fff"/><path d="m5 9 3 3 5-6" stroke="#0a56b8" stroke-width="2" fill="none"/></svg>Pedestrian Training Course</li>
      <li><svg class="tick" viewBox="0 0 18 18"><circle cx="9" cy="9" r="9" fill="#fff"/><path d="m5 9 3 3 5-6" stroke="#0a56b8" stroke-width="2" fill="none"/></svg>Pivot Steer Training Course</li>
      <li><svg class="tick" viewBox="0 0 18 18"><circle cx="9" cy="9" r="9" fill="#fff"/><path d="m5 9 3 3 5-6" stroke="#0a56b8" stroke-width="2" fill="none"/></svg>Reach Training Course</li>
      <li><svg class="tick" viewBox="0 0 18 18"><circle cx="9" cy="9" r="9" fill="#fff"/><path d="m5 9 3 3 5-6" stroke="#0a56b8" stroke-width="2" fill="none"/></svg>Rough Terrain Training Course</li>
      <li><svg class="tick" viewBox="0 0 18 18"><circle cx="9" cy="9" r="9" fill="#fff"/><path d="m5 9 3 3 5-6" stroke="#0a56b8" stroke-width="2" fill="none"/></svg>Sideloader Training Course</li>
      <li><svg class="tick" viewBox="0 0 18 18"><circle cx="9" cy="9" r="9" fill="#fff"/><path d="m5 9 3 3 5-6" stroke="#0a56b8" stroke-width="2" fill="none"/></svg>Telescopic Handeler Training Course</li>
      <li><svg class="tick" viewBox="0 0 18 18"><circle cx="9" cy="9" r="9" fill="#fff"/><path d="m5 9 3 3 5-6" stroke="#0a56b8" stroke-width="2" fill="none"/></svg>Tow Tractor Training Course</li>
      <li><svg class="tick" viewBox="0 0 18 18"><circle cx="9" cy="9" r="9" fill="#fff"/><path d="m5 9 3 3 5-6" stroke="#0a56b8" stroke-width="2" fill="none"/></svg>Vna Man Down&nbsp; Truck Training Course</li>
    </ul>
    <a class="btn-ghost" href="#" style="left:83px">LEARN MORE</a>
  </div>

  <div class="abs course-col col-mewp">
    <svg class="col-icon" style="left:58px" width="54" height="54" viewBox="0 0 54 54" fill="none" stroke="#fff" stroke-width="2.4"><path d="M6 4h42v10H6zM14 4v10M22 4v10M30 4v10M38 4v10M12 18l30 10M42 18 12 28M12 28l30 10M42 28 12 38M6 40h42v6H6z"/><circle cx="12" cy="50" r="3"/><circle cx="42" cy="50" r="3"/></svg>
    <h3 style="left:54px">MEWP TRAINING COURSES</h3>
    <ul class="course-list" style="left:58px">
      <li><svg class="tick" viewBox="0 0 18 18"><circle cx="9" cy="9" r="9" fill="#fff"/><path d="m5 9 3 3 5-6" stroke="#05aaf0" stroke-width="2" fill="none"/></svg>Cherry Picker Training Course</li>
      <li><svg class="tick" viewBox="0 0 18 18"><circle cx="9" cy="9" r="9" fill="#fff"/><path d="m5 9 3 3 5-6" stroke="#05aaf0" stroke-width="2" fill="none"/></svg>Scissor Lift Training Course</li>
      <li><svg class="tick" viewBox="0 0 18 18"><circle cx="9" cy="9" r="9" fill="#fff"/><path d="m5 9 3 3 5-6" stroke="#05aaf0" stroke-width="2" fill="none"/></svg>Harness And Lanyard Training Course</li>
    </ul>
    <a class="btn-ghost" href="#" style="left:39px">LEARN MORE</a>
  </div>

  <div class="abs course-col col-other">
    <svg class="col-icon" style="left:50px;top:28px" width="44" height="58" viewBox="0 0 44 58"><path d="M22 2a20 20 0 0 1 20 20c0 14-20 34-20 34S2 36 2 22A20 20 0 0 1 22 2z" fill="#fff"/><circle cx="22" cy="22" r="11" fill="none" stroke="#2c3a4d" stroke-width="3"/><circle cx="22" cy="22" r="3" fill="#2c3a4d"/><path d="M11 22h22M22 25v8" stroke="#2c3a4d" stroke-width="3"/></svg>
    <h3 style="left:51px">OTHER TRAINING COURSES</h3>
    <ul class="course-list" style="left:53px;top:152px">
      <li><svg class="tick" viewBox="0 0 18 18"><circle cx="9" cy="9" r="9" fill="#fff"/><path d="m5 9 3 3 5-6" stroke="#2c3a4d" stroke-width="2" fill="none"/></svg>Brakka Truck Training&nbsp; Course</li>
      <li><svg class="tick" viewBox="0 0 18 18"><circle cx="9" cy="9" r="9" fill="#fff"/><path d="m5 9 3 3 5-6" stroke="#2c3a4d" stroke-width="2" fill="none"/></svg>Front Loading Shovel TrainingCourse</li>
      <li><svg class="tick" viewBox="0 0 18 18"><circle cx="9" cy="9" r="9" fill="#fff"/><path d="m5 9 3 3 5-6" stroke="#2c3a4d" stroke-width="2" fill="none"/></svg>Overhead&nbsp; Pendant Crane Training Course</li>
      <li><svg class="tick" viewBox="0 0 18 18"><circle cx="9" cy="9" r="9" fill="#fff"/><path d="m5 9 3 3 5-6" stroke="#2c3a4d" stroke-width="2" fill="none"/></svg>Swing Colum Jib Crane Training Course</li>
      <li><svg class="tick" viewBox="0 0 18 18"><circle cx="9" cy="9" r="9" fill="#fff"/><path d="m5 9 3 3 5-6" stroke="#2c3a4d" stroke-width="2" fill="none"/></svg>Slingingand Signalling Training Course</li>
      <li><svg class="tick" viewBox="0 0 18 18"><circle cx="9" cy="9" r="9" fill="#fff"/><path d="m5 9 3 3 5-6" stroke="#2c3a4d" stroke-width="2" fill="none"/></svg>Vehicle Banksman&nbsp; Training Course</li>
    </ul>
    <a class="btn-ghost" href="#" style="left:50px">LEARN MORE</a>
  </div>
</section>

<section class="abs accred">
  <div class="abs eyebrow" style="left:0;width:1200px;text-align:center;top:62px;font-size:16px">FORKLIFT CERTIFICATE</div>
  <h2 class="abs" style="left:0;width:1200px;text-align:center;top:88px;font-weight:800;font-size:24px;color:var(--sky)">FORKLIFT TRAINING ACCREDITATION</h2>
  <div class="abs" style="left:560px;top:125px;width:70px;height:4px;background:var(--navy)"></div>
  <svg class="abs" style="left:310px;top:140px" width="580" height="90" viewBox="0 0 580 90" fill="none" stroke="#cfd9e6" stroke-width="2"><path d="M280 0v20a22 22 0 0 1-22 22H36A22 22 0 0 0 14 64v24M300 0v20a22 22 0 0 0 22 22h222a22 22 0 0 1 22 22v24"/></svg>
</section>

<div class="abs accred-card" style="left:108px">
  <div class="abs" style="left:31px;top:20px;width:98px;height:98px;background:#1e2a6e" aria-label="Certificate badge"></div>
  <div class="abs" style="left:31px;top:122px;font-weight:700;font-size:8px;color:#1e2a6e">PLOMVEX</div>
  <p style="top:145px">PLOMVEX is recognised throughout the united kingdom and Ireland as one of the leading material handling equipment training accrediting bodies. PLOMVEX is a founder member of the TWA (accrediting bodies association for workplace transport) and this replaced the accrediting bodies forum previously run by the NWSB. They have over 40 years experience of setting training standards,accreditation and monitoring. The PLOMVEX accreditation schemes are supported by legal requirements for training.</p>
</div>
<div class="abs accred-card" style="left:608px">
  <div class="abs partner-name" style="left:36px;top:36px">Tarnel</div>
  <p style="top:136px">We are accredited by the PLOMVEX who are recognised by the national workplace safety board as competent to deliver forklift truck operator training courses. As an PLOMVEX accredited training provider we are monitored annually to ensure we are maintaining our high standards as laid down by the PLOMVEX. All our instructors are qualified and registered with the PLOMVEX and monitored. Please note we are only accredited to deliver training at customer premises as we do not have a training centre.</p>
</div>

<section>
  <svg class="abs contact-photo" viewBox="0 0 567 589" role="img" aria-label="Young woman and man in hard hats at a forklift steering wheel">
    <defs><linearGradient id="photoTone" x1="0" y1="0" x2="1" y2="1"><stop offset="0" stop-color="#6f7f8c"/><stop offset=".5" stop-color="#a3786a"/><stop offset="1" stop-color="#4d5f7a"/></linearGradient></defs>
    <path d="M0 0h385a300 300 0 0 1 0 589H0z" fill="var(--sky)"/>
    <path d="M0 0h375a292 292 0 0 1 0 589H0z" fill="url(#photoTone)"/>
  </svg>
  <div class="abs eyebrow" style="left:647px;top:2895px;color:var(--sky);font-size:16px">GET IN TOUCH</div>
  <h2 class="abs" style="left:647px;top:2922px;font-weight:800;font-size:29px;color:var(--ink)">CONTACT US FORM</h2>
  <div class="abs" style="left:649px;top:2966px;width:76px;height:4px;background:var(--sky)"></div>
  <div class="abs field" style="top:2995px">YOUR NAME</div>
  <div class="abs field" style="top:3049px;left:651px">E-MAIL</div>
  <div class="abs field" style="top:3099px;left:652px">PHONE</div>
  <div class="abs field" style="top:3149px;left:653px;height:90px">LEAVE MESSAGE</div>
  <a class="abs btn-submit" href="#">SUBMIT MESSAGE</a>
</section>

<footer class="abs site-footer">
  <nav class="footer-nav">
    <a href="#" style="left:357px">HOME</a>
    <a href="#" style="left:469px">ABOUT US</a>
    <a href="#" style="left:608px">COURSES</a>
    <a href="#" style="left:742px">CONTACT US</a>
  </nav>
  <div class="copyright">2020 © COPYRIGHT DEI KVW TRAINING LTD RIGHTS RESERVED.</div>
  <span class="social-dot" style="left:558px" aria-label="Social link"></span>
  <span class="social-dot" style="left:587px" aria-label="Social link"></span>
  <span class="social-dot" style="left:616px" aria-label="Social link"></span>
</footer>

</body>
</html>
```